Business Cards for IT Consulting Company (Managed Service Provider)

I am looking to have some business cards printed and would like some designs. We are an IT Consulting company based in Vancouver BC. I would like a nice clean and modern look to the cards. I have uploaded all the versions of my logo so parts can be used as needed. Here is a snippit from our website homepage:

Quillbrook Networks Ltd. is an IT Solutions Partner located in Vancouver BC, Canada. We offer IT solutions and support to customers in the greater Vancouver Area. With expertise in Microsoft platforms, as well as Linux and Mac OSX and over 12 years experience in the IT industry, Quillbrook Networks is dedicated to offering our clients top quality service and products. We take pride in the solutions we offer our customers. The greatest compliment a client can give us is to recommend our services.

Quillbrook Networks Ltd. offers a wide range of IT services from onsite service to remote support and managed service solutions. This allows clients to choose the support path that best suits their company’s needs. Supporting many different sized companies from small to enterprise level over the past 12 years Quillbrook Networks has the experience and expertise needed to ensure things run smoothly. Allowing our clients to focus on doing business.

Revolutionizing the way IT services are delivered.

Quillbrook Networks is dedicated to providing our clients with IT solutions that work and grow with them for years to come. This philosophy helps save money in the long run instead of replacing equipment constantly. Far too often IT solutions are not well thought out and while possibly solving the problem at hand, require replacement due to growth or quality within a very short time frame. Quillbrook Networks takes pride in providing solutions that will last and be able to accommodate growth without the need for replacement.

Industry/Entity Type

Information Technology

Contact Information for Business Card

Quillbrook Networks Ltd.
(Employee Name)
Eml: (Employees Email Address)
Web: quillbrook.me
Ph: 604-555-0148

Font styles to use
Serif
Sans Serif

Requirements
Must have
• The Company logo and company colors.
Nice to have
• - Our tag line: "Revolutionizing IT Services" or "Revolutionizing the way IT services are delivered."
• - Also I really like the idea of nature and technology together blending which is sort of where my logo came from so integrating that somehow onto the business cards would be great.

```html
<!DOCTYPE html>
<html lang="en">
<head>
<meta charset="utf-8">
<title>Quillbrook Networks Ltd. – Business Card</title>
<link rel="stylesheet" href="https://fonts.googleapis.com/css2?family=Source+Sans+3:wght@400;600;700&display=swap">
<style>
  :root {
    --page-bg: #e9ecef;
    --card-blue-deep: #0d5fa6;
    --card-blue-mid: #2a86cf;
    --card-blue-light: #5aa9e0;
    --hex-frost: #eef3f7;
    --hex-frost-edge: #d7e2ea;
    --text-light: #ffffff;
    --text-soft: #e6f1fa;
    --brand-navy: #1d3f5e;
  }
  html, body {
    margin: 0;
    width: 1200px;
    height: 969px;
    overflow: hidden;
    background: var(--page-bg);
    font-family: "Source Sans 3", "Myriad Pro", sans-serif;
  }
  .card {
    position: absolute;
    left: 100px;
    top: 200px;
    width: 1000px;
    height: 570px;
    background: linear-gradient(110deg, var(--card-blue-deep) 0%, var(--card-blue-mid) 45%, var(--card-blue-light) 70%, var(--card-blue-deep) 100%);
    box-shadow: 0 10px 30px rgba(0, 0, 0, 0.18);
    overflow: hidden;
  }
  .hex-panel {
    position: absolute;
    inset: 0;
  }
  .contact {
    position: absolute;
    left: 52px;
    top: 150px;
    color: var(--text-soft);
  }
  .contact__name {
    margin: 0 0 30px;
    font-size: 40px;
    font-weight: 600;
    color: var(--text-light);
    line-height: 1;
  }
  .contact__address {
    margin: 0 0 26px;
    font-size: 26px;
    line-height: 36px;
  }
  .contact__list {
    list-style: none;
    margin: 0;
    padding: 0;
    font-size: 26px;
    line-height: 39px;
  }
  .contact__list li {
    display: flex;
    align-items: center;
    gap: 14px;
  }
  .contact__icon {
    width: 24px;
    height: 24px;
    fill: var(--text-soft);
    flex: none;
  }
  .brand {
    position: absolute;
    left: 422px;
    width: 543px;
    top: 250px;
    text-align: center;
    display: flex;
    justify-content: center;
    align-items: center;
    gap: 16px;
  }
  .brand__mark {
    width: 22px;
    height: 22px;
    background: var(--brand-navy);
    border-radius: 50%;
  }
  .brand__name {
    font-size: 40px;
    font-weight: 700;
    color: var(--brand-navy);
    line-height: 1;
  }
</style>
</head>
<body>
  <div class="card">
    <svg class="hex-panel" width="1000" height="570" viewBox="0 0 1000 570" aria-hidden="true">
      <defs>
        <linearGradient id="frost" x1="0" y1="0" x2="0" y2="1">
          <stop offset="0" stop-color="var(--hex-frost)"/>
          <stop offset="1" stop-color="var(--hex-frost-edge)"/>
        </linearGradient>
      </defs>
      <polygon points="422,285 585,54 797,54 965,285 797,516 585,516" fill="url(#frost)"/>
    </svg>

    <div class="contact">
      <h1 class="contact__name">Dana Morrow</h1>
      <p class="contact__address">4120 Fernhill Road<br>Vancouver, BC V5K 0A1</p>
      <ul class="contact__list">
        <li>
          <svg class="contact__icon" viewBox="0 0 24 24" aria-hidden="true"><path d="M6.6 10.8a15.1 15.1 0 0 0 6.6 6.6l2.2-2.2c.3-.3.7-.4 1-.2 1.1.4 2.3.6 3.6.6.6 0 1 .4 1 1V20c0 .6-.4 1-1 1A17 17 0 0 1 3 4c0-.6.4-1 1-1h3.5c.6 0 1 .4 1 1 0 1.3.2 2.5.6 3.6.1.3 0 .7-.2 1z"/></svg>
          <span>604-555-0148</span>
        </li>
        <li>
          <svg class="contact__icon" viewBox="0 0 24 24" aria-hidden="true"><path d="M2 5h20v14H2z M2 5l10 8 10-8" fill="none" stroke="var(--text-soft)" stroke-width="2"/><path d="M2 6l10 7.5L22 6V19H2z"/></svg>
          <span>dmorrow@quillbrook.me</span>
        </li>
        <li>
          <svg class="contact__icon" viewBox="0 0 24 24" aria-hidden="true"><circle cx="12" cy="12" r="10" fill="none" stroke="var(--text-soft)" stroke-width="2"/><path d="M2 12h20M12 2c3 3 3 17 0 20M12 2c-3 3-3 17 0 20" fill="none" stroke="var(--text-soft)" stroke-width="1.6"/></svg>
          <span>www.quillbrook.me</span>
        </li>
      </ul>
    </div>

    <div class="brand">
      <span class="brand__mark"></span>
      <span class="brand__name">Quillbrook Networks Ltd.</span>
    </div>
  </div>
</body>
</html>
```